Need Business Card ASAP

We need a business card design for a meeting coming up in a few days. The company name is Harlow Ridge Building and Construction and the logo is attached. Something clean, cool, and contemporary that we can get to a printer right away. Attached is the business card for Volmar Energy, an affiliated company, which we like. Instead of the hawk on the back, you could use the attached "D". We'll also be needing matching letterhead in the near future, so ideas for that are welcome.

```html
<!DOCTYPE html>
<html lang="en">
<head>
<meta charset="utf-8">
<title>Harlow Ridge Building and Construction – Business Card</title>
<link rel="stylesheet" href="https://fonts.googleapis.com/css2?family=Source+Sans+3:wght@400;600;700&display=swap">
<style>
  :root {
    --page: #6e5538;
    --khaki: #c9c595;
    --khaki-light: #e4e2c6;
    --khaki-text: #b5ae72;
    --ink: #2a2a2a;
    --grey: #444444;
    --white: #ffffff;
    --divider: #bdbdbd;
  }
  * { margin: 0; padding: 0; box-sizing: border-box; }
  html, body { width: 1034px; height: 1200px; overflow: hidden; }
  body {
    background: var(--page);
    font-family: "Source Sans 3", Arial, sans-serif;
    color: var(--ink);
    position: relative;
  }
  .card {
    position: absolute;
    left: 73px;
    width: 885px;
    height: 504px;
    overflow: hidden;
    box-shadow: 0 3px 10px rgba(0,0,0,.35);
  }
  .card--front { top: 59px; background: var(--white); }
  .card--back { top: 600px; background: var(--khaki); }

  .front__band { position: absolute; inset: 0; width: 885px; height: 504px; }
  .front__company {
    position: absolute; top: 30px; width: 100%; text-align: center;
    font-size: 29px; font-weight: 700; color: var(--ink);
  }
  .front__address {
    position: absolute; top: 68px; width: 100%; text-align: center;
    font-size: 21px; color: var(--ink);
  }
  .brand {
    position: absolute; left: 159px; top: 210px; width: 190px; height: 233px;
    display: flex; flex-direction: column; align-items: center; justify-content: center; gap: 18px;
  }
  .brand__mark { width: 56px; height: 56px; background: var(--ink); }
  .brand__name {
    font-size: 30px; font-weight: 700; color: var(--ink); text-align: center; line-height: 1.1;
  }
  .divider {
    position: absolute; left: 375px; top: 203px; width: 3px; height: 246px;
    background: linear-gradient(to bottom, rgba(189,189,189,0), var(--divider) 30%, var(--divider) 70%, rgba(189,189,189,0));
  }
  .person { position: absolute; left: 403px; top: 202px; }
  .person__name { font-size: 34px; font-weight: 700; color: var(--khaki-text); line-height: 1.1; }
  .person__title { font-size: 22px; font-weight: 600; color: var(--grey); margin-top: 4px; }
  .contact { list-style: none; position: absolute; left: 403px; top: 292px; }
  .contact__item {
    display: flex; align-items: center; gap: 10px;
    font-size: 25px; color: var(--grey); height: 42px;
  }
  .contact__icon { width: 18px; height: 18px; flex: none; }

  .back__name {
    position: absolute; left: 70px; top: 150px; display: flex; align-items: center; gap: 20px;
  }
  .back__mark { width: 70px; height: 70px; background: var(--white); }
  .back__brand { font-size: 44px; font-weight: 700; color: var(--white); line-height: 1.05; }
  .back__web {
    position: absolute; left: 459px; top: 236px;
    font-size: 25px; font-weight: 700; color: var(--grey);
  }
</style>
</head>
<body>
  <section class="card card--front">
    <svg class="front__band" viewBox="0 0 885 504" aria-hidden="true">
      <defs>
        <linearGradient id="bandFill" x1="0" y1="0" x2="1" y2="1">
          <stop offset="0" stop-color="#c6c290"/>
          <stop offset="1" stop-color="#e6e4cc"/>
        </linearGradient>
      </defs>
      <path d="M0 0 H885 V135 C700 70 420 50 0 160 Z" fill="url(#bandFill)"/>
    </svg>
    <h1 class="front__company">Harlow Ridge Building and Construction</h1>
    <p class="front__address">00, Complex Name, Street, City 00000</p>

    <div class="brand">
      <span class="brand__mark"></span>
      <span class="brand__name">Harlow Ridge</span>
    </div>
    <span class="divider"></span>

    <div class="person">
      <p class="person__name">Your Name</p>
      <p class="person__title">Title</p>
    </div>
    <ul class="contact">
      <li class="contact__item">
        <svg class="contact__icon" viewBox="0 0 20 20"><path d="M5 2l3 4-2 2c1 2 3 4 5 5l2-2 4 3-2 3C9 17 3 11 2 5z" fill="none" stroke="#444" stroke-width="1.6"/></svg>
        (123) 456-7890
      </li>
      <li class="contact__item">
        <svg class="contact__icon" viewBox="0 0 20 20"><rect x="5" y="1" width="10" height="18" rx="2" fill="none" stroke="#444" stroke-width="1.6"/><rect x="7" y="4" width="6" height="8" fill="#444"/></svg>
        (123) 456-7890
      </li>
      <li class="contact__item">
        <svg class="contact__icon" viewBox="0 0 20 20"><path d="M2 8l8-5 8 5v9H2z" fill="#444"/><path d="M2 8l8 5 8-5" fill="none" stroke="#fff" stroke-width="1.4"/></svg>
        yourname@harlowridge.com
      </li>
      <li class="contact__item">
        <svg class="contact__icon" viewBox="0 0 20 20"><circle cx="10" cy="10" r="8" fill="none" stroke="#444" stroke-width="1.6"/><ellipse cx="10" cy="10" rx="3.5" ry="8" fill="none" stroke="#444" stroke-width="1.4"/><path d="M2 10h16M4 5.5h12M4 14.5h12" stroke="#444" stroke-width="1.2"/></svg>
        www.harlowridge.com
      </li>
    </ul>
  </section>

  <section class="card card--back">
    <div class="back__name">
      <span class="back__mark"></span>
      <span class="back__brand">Harlow<br>Ridge</span>
    </div>
    <p class="back__web">www.harlowridgebuilding.com</p>
  </section>
</body>
</html>
```